Communication and Marketing agency needs a new presentation card

We are a group of communication and marketing agencies specialized in companies that are in the logistics and industrial sector. The head agency is TELVANO Grupo and the group consists of 4 agencies: TELVANO Media, TELVANO Digital, TELVANO Research and DifundeEnPantalla. We hace 4 offices in Spain (Madrid, Barcelona, Valencia and Murcia). We are looking for a clean and attractive design that transmits our experience, brand presence in the market and knowledge to those who receive the card.It has to maintain the colors of the logo that is attached.
Target Market(s)
logistics and industrial sector
Marketing department
Contact Information for Business Card
Clean and attractive design

```html
<!DOCTYPE html>
<html lang="es">
<head>
<meta charset="utf-8">
<title>TELVANO Grupo – Tarjeta de visita</title>
<link rel="stylesheet" href="https://fonts.googleapis.com/css2?family=Roboto:wght@400;500;700&display=swap">
<style>
  :root {
    --brand-red: #b0222a;
    --ink-grey: #4a4746;
    --text-grey: #4d4d4d;
    --card-white: #ffffff;
    --backdrop: #e4e4e4;
  }
  * { margin: 0; padding: 0; box-sizing: border-box; }
  html, body {
    width: 1125px; height: 1200px; overflow: hidden;
    background: var(--backdrop);
    font-family: "Roboto", Arial, sans-serif;
  }
  .canvas { position: relative; width: 1125px; height: 1200px; }

  .card {
    position: absolute; left: 172px; width: 825px; height: 472px;
    background: var(--card-white);
    box-shadow: 0 2px 4px rgba(0,0,0,0.25);
  }
  .card--front { top: 106px; }
  .card--back { top: 639px; }

  /* front */
  .brand-lockup {
    position: absolute; right: 56px; top: 56px; text-align: right;
    color: var(--brand-red); font-weight: 500; line-height: 1;
  }
  .brand-lockup__name { font-size: 62px; letter-spacing: 2px; display: block; }
  .brand-lockup__unit { font-size: 34px; display: block; margin-top: 4px; }

  .accent-tab {
    position: absolute; left: 0; top: 193px; width: 19px; height: 52px;
    background: var(--ink-grey);
  }
  .person { position: absolute; left: 57px; top: 188px; }
  .person__name { font-size: 29px; font-weight: 700; color: var(--brand-red); line-height: 1.1; }
  .person__role { font-size: 19px; font-weight: 500; color: var(--text-grey); margin-top: 2px; }

  .contact-list { position: absolute; left: 57px; top: 265px; list-style: none; }
  .contact-list li {
    display: flex; align-items: center; height: 26px;
    font-size: 19px; color: var(--text-grey);
  }
  .contact-list svg { width: 18px; height: 18px; margin-right: 12px; fill: var(--brand-red); flex: none; }

  .office-band {
    position: absolute; left: 0; right: 0; top: 410px; height: 36px;
    background: var(--brand-red); color: #fff;
    font-size: 19px; line-height: 36px; padding-left: 57px;
  }

  /* back */
  .group-lockup {
    position: absolute; left: 186px; top: 138px; width: 424px; text-align: right;
    color: var(--brand-red); font-weight: 500; line-height: 1;
  }
  .group-lockup__name { display: block; font-size: 80px; letter-spacing: 3px; }
  .group-lockup__unit { display: block; font-size: 46px; margin-top: 10px; }

  .agency-band {
    position: absolute; left: 0; right: 0; top: 359px; height: 80px;
    background: var(--brand-red);
    display: flex; justify-content: space-around; align-items: center;
    padding: 0 20px;
  }
  .agency {
    color: #fff; font-weight: 500; text-align: right; line-height: 1;
  }
  .agency__name { display: block; font-size: 26px; letter-spacing: 1px; }
  .agency__unit { display: block; font-size: 17px; margin-top: 3px; }
  .agency--single .agency__name { font-size: 21px; letter-spacing: 0; }
</style>
</head>
<body>
<main class="canvas">

  <section class="card card--front" aria-label="Anverso de la tarjeta">
    <div class="brand-lockup">
      <span class="brand-lockup__name">TELVANO</span>
      <span class="brand-lockup__unit">Media</span>
    </div>

    <div class="accent-tab"></div>
    <div class="person">
      <h1 class="person__name">Ramiro Estévez</h1>
      <p class="person__role">Director</p>
    </div>

    <ul class="contact-list">
      <li>
        <svg viewBox="0 0 24 24" aria-hidden="true"><path d="M6.6 10.8a15.1 15.1 0 0 0 6.6 6.6l2.2-2.2c.3-.3.7-.4 1-.2 1.1.4 2.3.6 3.6.6.6 0 1 .4 1 1V20c0 .6-.4 1-1 1A17 17 0 0 1 3 4c0-.6.4-1 1-1h3.5c.6 0 1 .4 1 1 0 1.3.2 2.5.6 3.6.1.3 0 .7-.2 1z"/></svg>
        910 555 214
      </li>
      <li>
        <svg viewBox="0 0 24 24" aria-hidden="true"><path d="M7 1h10a2 2 0 0 1 2 2v18a2 2 0 0 1-2 2H7a2 2 0 0 1-2-2V3a2 2 0 0 1 2-2zm0 3v14h10V4zm5 15.2a1.1 1.1 0 1 0 0 2.2 1.1 1.1 0 0 0 0-2.2z"/></svg>
        600 555 471
      </li>
      <li>
        <svg viewBox="0 0 24 24" aria-hidden="true"><path d="M2 5h20v14H2zm2 2v.4l8 5 8-5V7zm0 2.7V17h16V9.7l-8 5z"/></svg>
        restevez@telvano.es
      </li>
      <li>
        <svg viewBox="0 0 24 24" aria-hidden="true"><rect x="3" y="3" width="18" height="18" rx="2"/></svg>
        ramiroestevez
      </li>
      <li>
        <svg viewBox="0 0 24 24" aria-hidden="true"><path d="M12 2a10 10 0 1 0 0 20 10 10 0 0 0 0-20zm-1 17.9A8 8 0 0 1 4.2 10.8L9 15.6v1a2 2 0 0 0 2 2zm6.9-2.5a2 2 0 0 0-1.9-1.4h-1v-3a1 1 0 0 0-1-1H8v-2h2a1 1 0 0 0 1-1V7h2a2 2 0 0 0 2-2v-.4a8 8 0 0 1 2.9 12.8z"/></svg>
        telvano.es
      </li>
    </ul>

    <div class="office-band">Madrid • Barcelona • Valencia • Murcia</div>
  </section>

  <section class="card card--back" aria-label="Reverso de la tarjeta">
    <div class="group-lockup">
      <span class="group-lockup__name">TELVANO</span>
      <span class="group-lockup__unit">Grupo</span>
    </div>

    <div class="agency-band">
      <div class="agency"><span class="agency__name">TELVANO</span><span class="agency__unit">Digital</span></div>
      <div class="agency"><span class="agency__name">TELVANO</span><span class="agency__unit">Media</span></div>
      <div class="agency"><span class="agency__name">TELVANO</span><span class="agency__unit">Research</span></div>
      <div class="agency agency--single"><span class="agency__name">DIFUNDE</span><span class="agency__name">ENPANTALLA</span></div>
    </div>
  </section>

</main>
</body>
</html>
```